Webdesign für neue Weinmarke
Zielgruppe
Kelchwandler ist eine neue Weinmarke. Es wird vorerst drei grundlegende Sorten geben: einen Rotwein, einen Weißwein und einen Rosé. Für diese neue Weinmarke wollen wir eine Webseite gestalten, welche die Weine ansprechend darstellt und zusätzlich den Kunden die Möglichkeit gibt, mehr Informationen über den Wein einzuholen. Die Marke Kelchwandler ist auch im Etikett an den Graf von Tressenbach angelehnt. Das Etikett zeigt den Baron, wie er auf einem Weinfass reitet – daher der Name „Kelchwandler“. Die Story, die wir mit dem Wein spielen, ist, dass die besonderen Fähigkeiten des Barons auch auf den Genuss des Kelchwandler zurückzuführen sind.
Die Zielgruppe für den Kelchwandler ist breit gefächert und schließt per se erst mal keine Personengruppe aus. Der Wein soll eher im niedrigeren Preissegment verkauft werden.
Aufgabenstellung
Es soll eine neue Webseite designt werden, die sich im Aufbau an der die Webseite http://www.velgor-example.de/#!/de/unsere-weine/sortiment orientieren kann. Zudem können für die Entwicklung kleine Animationen berücksichtigt werden, die die Seite auflockern. Das Design soll eine responsive Webseite unterstützen. Das Design soll zur Weinmarke Kelchwandler passen von der wir bisher nur das Etikett haben.

```html
<!DOCTYPE html>
<html lang="de">
<head>
<meta charset="utf-8">
<title>Kelchwandler Weißwein</title>
<link href="https://fonts.googleapis.com/css2?family=Cinzel:wght@400;700&family=Open+Sans:wght@400;600&display=swap" rel="stylesheet">
<style>
:root{
  --outer:#ececea;
  --paper:#f1efea;
  --sage:#d4dcab;
  --banner:#b3ba6a;
  --olive:#6d7547;
  --olive-soft:#8b9360;
  --ink:#2b2622;
  --brown:#8b7363;
  --brown-soft:#bfa89b;
  --muted:#a8a08f;
  --white:#ffffff;
}
*{margin:0;padding:0;box-sizing:border-box}
html,body{width:800px;height:1200px;overflow:hidden;background:var(--outer)}
body{position:relative;font-family:"Open Sans",sans-serif;color:var(--ink)}
.abs{position:absolute}
.page{position:absolute;left:47px;top:0;width:706px;height:1200px;background:var(--paper);overflow:hidden}
.hero{position:absolute;left:0;top:0;width:706px;height:378px}
.brand{position:absolute;left:150px;top:10px;width:100px;text-align:center}
.brand-dot{display:block;width:30px;height:30px;border-radius:50%;background:var(--brown-soft);margin:0 auto 6px}
.brand-name{font-family:"Cinzel",serif;font-weight:700;font-size:8px;color:var(--brown);letter-spacing:.3px}
.nav{position:absolute;left:277px;top:27px;font-family:"Cinzel",serif;font-size:6.6px;letter-spacing:.6px;display:flex;gap:6px;color:var(--ink)}
.nav .sep{color:var(--brown-soft)}
.nav .active{color:var(--muted);border-bottom:1px dotted var(--muted);padding-bottom:1px}
.submenu{position:absolute;right:224px;top:39px;font-family:"Cinzel",serif;font-size:6.4px;letter-spacing:.6px;text-align:right;line-height:9.3px}
.submenu .current{color:var(--muted)}
.sketch{position:absolute;left:23px;top:70px;width:675px;height:280px;border-radius:40%/30%;background:radial-gradient(ellipse at center,rgba(170,145,125,.28),rgba(170,145,125,.05) 70%,transparent)}
.hero-product{position:absolute;left:318px;top:68px;width:230px;height:327px;background:linear-gradient(90deg,rgba(120,170,60,.55) 0 35%,rgba(170,165,80,.7) 35% 70%,rgba(230,225,200,.6) 70%);border-radius:40px 40px 10px 10px}
.banner{position:absolute;left:149px;top:180px;width:287px;height:84px;background:var(--banner);opacity:.92;padding:18px 0 0 16px;color:var(--white)}
.banner h1{font-family:"Cinzel",serif;font-weight:400;font-size:21px;letter-spacing:.2px;line-height:1}
.banner p{font-family:"Cinzel",serif;font-size:8.5px;margin-top:3px}
.cta{display:flex;align-items:center;gap:6px;font-family:"Cinzel",serif;font-size:7.6px}
.cta::before,.cta::after{content:"";width:14px;height:1px;background:currentColor}
.banner .cta{margin-top:12px}
.detail{position:absolute;left:0;top:378px;width:706px;height:417px;background:var(--sage)}
.barrel{position:absolute;left:453px;top:22px;width:253px;height:365px;border-radius:50%/40%;background:radial-gradient(ellipse,rgba(140,155,95,.28),rgba(140,155,95,.05) 75%)}
.bottle-photo{position:absolute;left:173px;top:24px;width:80px;height:356px;border-radius:30px 30px 10px 10px;background:linear-gradient(180deg,#2c2a28 0 18%,#b3ad4a 18% 60%,#e6e6e2 60% 88%,#a9a548 88%)}
.tools{position:absolute;left:279px;top:25px;display:flex;gap:5px;align-items:center}
.back{position:absolute;left:533px;top:31px;font-family:"Cinzel",serif;font-size:5.5px;color:var(--olive-soft)}
.info{position:absolute;left:323px;top:52px;width:235px;color:var(--olive)}
.year{font-family:"Cinzel",serif;font-size:28px;line-height:1}
.kind{font-family:"Cinzel",serif;font-size:12px;margin-top:2px}
.rule{height:1px;background:var(--olive-soft);opacity:.7;position:relative}
.rule::after{content:"";position:absolute;right:-1px;top:-2px;width:5px;height:5px;border:1px solid var(--olive-soft);transform:rotate(45deg)}
.info h2{font-family:"Cinzel",serif;font-weight:400;font-size:9px;margin:11px 0 6px}
.info .text{font-size:5.5px;line-height:17px;color:#5f6640}
.facts{display:grid;grid-template-columns:105px 130px;row-gap:17px;margin-top:16px}
.fact{display:flex;gap:6px;align-items:center}
.fact svg{flex:none}
.fact b{display:block;font-family:"Cinzel",serif;font-weight:400;font-size:7.8px}
.fact span{display:block;font-size:5.6px;font-weight:600;color:#5a6238}
.fact.wide{grid-column:1 / 3}
.fact.wide span{font-weight:400}
.actions{display:flex;justify-content:space-between;margin-top:10px;color:var(--olive-soft)}
.more{position:absolute;left:0;top:795px;width:706px;height:405px}
.faint-art{position:absolute;left:0;top:75px;width:250px;height:285px;background:radial-gradient(ellipse at 35% 45%,rgba(200,185,170,.35),transparent 70%)}
.more h3{position:absolute;left:0;width:706px;top:18px;text-align:center;font-family:"Cinzel",serif;font-weight:400;font-size:16px;color:var(--brown);display:flex;justify-content:center;gap:8px;align-items:center}
.product{position:absolute;top:55px;width:130px;text-align:center}
.product .shot{width:48px;height:216px;margin:0 auto;border-radius:14px 14px 6px 6px}
.shot.red{background:linear-gradient(180deg,#1f1c1c 0 22%,#3a2428 22% 60%,#eeeae6 60% 90%,#2d1f22 90%)}
.shot.rose{background:linear-gradient(180deg,#1f1c1c 0 18%,#d85a68 18% 60%,#eeeae6 60% 90%,#c84a58 90%)}
.product h4{font-family:"Cinzel",serif;font-weight:400;font-size:8.6px;color:var(--brown-soft);margin-top:18px}
.product p{font-size:5.4px;color:var(--brown);margin-top:3px;letter-spacing:.2px}
.product .cta{justify-content:center;color:var(--brown-soft);font-size:6.4px;margin-top:8px}
.divider{position:absolute;left:352px;top:127px;width:1px;height:73px;background:var(--brown-soft)}
.footer-band{position:absolute;left:0;top:1135px;width:706px;height:65px;background:linear-gradient(180deg,rgba(168,151,138,.5),#a8978a 35%)}
.copyright{position:absolute;left:150px;top:1185px;font-size:4.6px;color:var(--white)}
.legal{position:absolute;left:481px;top:1183px;font-size:4.6px;color:var(--white);display:flex;gap:4px;align-items:center}
.legal i{width:7px;height:7px;background:var(--white);display:inline-block}
</style>
</head>
<body>
<div class="page">
  <section class="hero">
    <div class="sketch" role="img" aria-label="Federzeichnung eines Schlosses mit Türmen und Weinbergen"></div>
    <div class="hero-product" role="img" aria-label="Weißweinflasche mit Trauben, Weinglas und Schreibfeder"></div>
    <div class="brand"><span class="brand-dot"></span><span class="brand-name">KELCHWANDLER</span></div>
    <nav class="nav">
      <span>KELCHWANDLER</span><span class="sep">◆</span>
      <span>GESCHICHTEN DES GRAFEN</span><span class="sep">◆</span>
      <span class="active">UNSERE WEINE</span><span class="sep">◆</span>
      <span>PRESS</span><span class="sep">◆</span>
      <span>KONTAKT</span>
    </nav>
    <div class="submenu"><div>ROTWEIN</div><div class="current">WEISSWEIN</div><div>ROSÉ</div></div>
    <div class="banner">
      <h1>KELCHWANDLER WEISSWEIN</h1>
      <p>DES KELCHWANDLERS PFÄLZER RIESLING</p>
      <div class="cta">JETZT BESTELLEN</div>
    </div>
  </section>

  <section class="detail">
    <div class="barrel" role="img" aria-label="Blasse Zeichnung eines Weinfasses"></div>
    <div class="bottle-photo" role="img" aria-label="Flasche Riesling feinherb"></div>
    <div class="tools">
      <svg width="14" height="10" viewBox="0 0 14 10"><ellipse cx="7" cy="6" rx="6" ry="3" fill="none" stroke="#8b9360" stroke-width=".8"/><text x="7" y="5" font-size="4.5" text-anchor="middle" fill="#8b9360" font-family="sans-serif">360°</text></svg>
      <span style="width:1px;height:8px;background:#8b9360;opacity:.5"></span>
      <svg width="11" height="11" viewBox="0 0 11 11"><circle cx="7" cy="4" r="3" fill="none" stroke="#8b9360" stroke-width=".9"/><line x1="5" y1="6" x2="1" y2="10" stroke="#8b9360" stroke-width="1"/></svg>
    </div>
    <div class="back">ZURÜCK</div>
    <div class="info">
      <div class="year">2016</div>
      <div class="kind">DEUTSCHER QUALITÄTSWEIN</div>
      <div class="rule" style="margin-top:7px"></div>
      <h2>CHARAKTERISTIK</h2>
      <div class="text">
        Des Kelchwandlers Pfälzer Riesling hat wahrlich wunderbare Harmonien.<br>
        Sein ermunternder Schwung verleiht Genießern, wie dem Grafen höchstselbst,<br>
        nicht nur Anmut, sondern auch Heldengeist.
      </div>
      <div class="rule" style="margin-top:4px"></div>
      <div class="facts">
        <div class="fact">
          <svg width="24" height="22" viewBox="0 0 24 22" fill="#8b9360"><circle cx="5" cy="9" r="2.6"/><circle cx="10" cy="9" r="2.6"/><circle cx="15" cy="9" r="2.6"/><circle cx="7.5" cy="13.5" r="2.6"/><circle cx="12.5" cy="13.5" r="2.6"/><circle cx="10" cy="18" r="2.6"/><path d="M15 6 Q19 2 23 4" stroke="#8b9360" fill="none"/></svg>
          <div><b>REBSORTE</b><span>RIESLING</span></div>
        </div>
        <div class="fact">
          <svg width="18" height="24" viewBox="0 0 18 24"><rect x="4" y="1" width="5" height="16" rx="2.5" fill="none" stroke="#8b9360"/><circle cx="6.5" cy="19" r="4" fill="#8b9360"/><path d="M12 4h4M12 7h4M12 10h4" stroke="#8b9360"/></svg>
          <div><b>TRINKTEMPERATUR</b><span>10-12 °C</span></div>
        </div>
        <div class="fact">
          <svg width="24" height="22" viewBox="0 0 24 22"><path d="M14 2h8l-1 6a3 3 0 0 1-6 0z" fill="none" stroke="#8b9360"/><line x1="18" y1="11" x2="18" y2="16" stroke="#8b9360"/><path d="M1 14h9l4 4H1z" fill="#8b9360"/></svg>
          <div><b>GESCHMACK</b><span>FEINHERB</span></div>
        </div>
        <div class="fact">
          <svg width="18" height="24" viewBox="0 0 18 24"><path d="M7 1l5 2 1 5 3 3-1 6 1 4-5 2-5-1-3-3 1-5-3-4 3-4z" fill="#8b9360"/></svg>
          <div><b>HERKUNFT</b><span>DEUTSCHLAND (PFALZ)</span></div>
        </div>
        <div class="fact wide">
          <svg width="24" height="20" viewBox="0 0 24 20"><path d="M5 12a8 8 0 0 1 16 0z" fill="#8b9360"/><line x1="3" y1="13" x2="23" y2="13" stroke="#8b9360"/><path d="M1 15h9l3 3H1z" fill="#8b9360"/></svg>
          <div><b>VERZEHREMPFEHLUNG</b><span>Hervorragend als Begleiter zu Fisch, Geflügel und hellem Fleisch.</span></div>
        </div>
      </div>
      <div class="rule" style="margin-top:10px"></div>
      <div class="actions"><div class="cta">JETZT BESTELLEN</div><div class="cta">FACTSHEET DRUCKEN</div></div>
    </div>
  </section>

  <section class="more">
    <div class="faint-art" role="img" aria-label="Blasse Zeichnung des Grafen mit erhobenem Weinglas"></div>
    <h3>
      <svg width="36" height="6" viewBox="0 0 36 6"><line x1="0" y1="3" x2="36" y2="3" stroke="#8b7363"/><path d="M30 0l6 3-6 3z" fill="#8b7363"/></svg>
      WEITERE PRODUKTE
      <svg width="36" height="6" viewBox="0 0 36 6"><line x1="0" y1="3" x2="36" y2="3" stroke="#8b7363"/><path d="M6 0L0 3l6 3z" fill="#8b7363"/></svg>
    </h3>
    <div class="product" style="left:218px">
      <div class="shot red" role="img" aria-label="Flasche Dornfelder halbtrocken"></div>
      <h4>KELCHWANDLER ROTWEIN</h4>
      <p>DES KELCHWANDLERS PFÄLZER DORNFELDER</p>
      <div class="cta">WINE DETAILS</div>
    </div>
    <div class="divider"></div>
    <div class="product" style="left:358px">
      <div class="shot rose" role="img" aria-label="Flasche Dornfelder Rosé"></div>
      <h4>KELCHWANDLER ROSÉ</h4>
      <p>DES KELCHWANDLERS LIEBLICHER ROSÉ</p>
      <div class="cta">WINE DETAILS</div>
    </div>
  </section>

  <div class="footer-band" role="img" aria-label="Pinselstrich-Fläche in Braungrau"></div>
  <div class="copyright">Copyright © 2018 Hellbach Getränke GmbH</div>
  <div class="legal"><span>IMPRESSUM</span><span>|</span><span>DATENSCHUTZ</span><i></i></div>
</div>
</body>
</html>
```